Dentistry Office

We want a new design for a Dentist's office website.

The theme is: "We provide high quality, state-of-the-art, dental care in a comfortable, caring environment."

The site currently has a menu on the left of the page with about 40 items on it. There is a great deal of textual content on each page, plus several illustrations.

We want to do this using CSS, so we need specifications in the CSS for all possible elements. The CSS needs to be named in a logical manner for easy use.

Every dentist on the planet seems to use lots of Flash. We don't want to because it is so distracting. We are looking for an elegant solution targeting 24-55 age group, but not excluding anyone.

The following (from another dentist's site) can give you a taste of what we want to communicate on the site:

"After 20 years of teaching dentists how to refine their technique and many years of writing textbooks, I currently devote my time to my office and the hands-on practice of dentistry. I'd like to welcome you personally to my dental practice, and I invite you to meet my highly experienced team of professionals.

"We have offered complete dental care of the highest quality since 1978. We provide Preventive Services, Tooth Whitening and Cosmetic Dentistry for a beautiful smile, Endodontics (root canal treatment) to treat painful teeth, Sedation Dentistry so you can relax, and Dental Implants to restore what is missing. We offer total care.

"Our approach to your health is simple: We use our education, experience and dedication to provide every patient with superior dental care.

"This passion for excellence is not just a goal, but a standard every member of our team holds.

"We also pride ourselves with our state of the art procedures, training and technology. This includes creating a beautiful smile using techniques that preserve as much of the original tooth as possible.

"Our abilities are renowned throughout the dental profession and I hope if you have any questions you will contact us by an e-mail note, by phone or just by dropping by."

Keep in mind the screen shape and dimensions. Your design needs to work in the normal screen proportions, regardless of how it looks when you post it here. Scrolling is OK, but the first impression needs to work.
Updates

Keep in mind that there will be about 250 words, or more, on each page.

Competitors web sites:

http://www.brindlecovedentist.example/

http://www.brindlecovedentalcare.example/

http://www.grinsbymarlowvaledental.example/

http://www.tenbyfamilydentalcare.example/

http://www.quelmardental.example/

http://www.dovrinadental.example/

We need to compete with these.

Target Market(s)

Generally adults seeking the most experienced and comfortable-to-be-with dentist.

Industry/Entity Type

Training

Requirements
Must have
• Must stand apart from other dentists.
• Must be elegant.
• Must have a horizontal menu structure across all columns, NOT a vertical that requires scrolling, no popout, pop down, etc. menus.
• We are looking for something special.
• Do not waste your time or ours putting up templates and things you have used before.
• Personally, I do not see how someone outside the US can understand the northern California dental market. But you are welcome to try.
Should not have
• Flash or graphics that move
• The look of a template
• Folksy fonts
• Looks like you used it 20 times before

```html
<!DOCTYPE html>
<html lang="en">
<head>
<meta charset="utf-8">
<title>Dentist's Office</title>
<link rel="stylesheet" href="https://fonts.googleapis.com/css2?family=Arimo:wght@400;700&display=swap">
<style>
:root{
  --blue:#0a9ddc;
  --blue-dark:#0786c0;
  --blue-text:#1a8fdc;
  --tab-active:#c8ebfa;
  --grey-text:#666;
  --grey-dark:#444;
  --grey-light:#999;
  --footer-bg:#e8f6fd;
  --white:#fff;
}
*{margin:0;padding:0;box-sizing:border-box}
html,body{width:1200px;height:900px;overflow:hidden;background:var(--white)}
body{font-family:"Arimo",Arial,sans-serif;color:var(--grey-text);position:relative}
.page{position:absolute;left:88px;top:42px;width:1024px;height:858px;
  background:linear-gradient(#fff 0,#ececee 118px,#f6f6f7 200px,#fff 340px);}
.abs{position:absolute}
a{color:inherit;text-decoration:none}

.brand{left:75px;top:39px;display:flex;align-items:center;gap:10px}
.brand-mark{width:48px;height:48px;background:var(--blue);border-radius:8px}
.brand-name{font-size:29px;color:#555;letter-spacing:-.8px}

.utility-links{left:768px;top:22px;display:flex;gap:24px;font-size:12px;color:#333}
.utility-links a::before{content:"\25B6";color:var(--blue);font-size:7px;margin-right:3px;vertical-align:2px}
.search{left:767px;top:61px;width:183px;height:19px;border:1px solid #bbb;background:#fff;
  font-size:11px;color:#aaa;padding:3px 8px}
.search svg{position:absolute;right:7px;top:3px}

.main-nav{left:0;top:118px;width:1024px;height:28px;
  background:linear-gradient(var(--blue) 0,var(--blue) 15px,var(--blue-dark) 15px,var(--blue) 28px);}
.main-nav a{position:absolute;top:6px;font-size:14px;color:var(--white)}
.main-nav .caret{font-size:9px;margin-right:4px;vertical-align:1px}
.main-nav .active{top:1px;left:529px;width:99px;height:27px;padding:5px 0 0 6px;
  background:var(--tab-active);border-radius:6px 6px 0 0;color:#333}
.main-nav .active .caret{color:var(--blue)}

.breadcrumb{left:83px;top:153px;font-size:10.5px;color:var(--grey-light);display:flex;gap:16px}
.breadcrumb span::before{content:"\25B6";font-size:7px;margin-right:3px}
.breadcrumb .current{color:var(--blue-text)}

.page-title{left:77px;top:220px;font-size:26px;font-weight:400;color:#666}
.lead{left:77px;top:272px;width:680px;font-size:16.8px;color:var(--blue-text);line-height:30px}
.lead span{display:inline-block;border-bottom:1px dotted #bbb;line-height:28px}

.photo{left:84px;top:388px;width:116px;height:98px;border:5px solid #fff;border-radius:8px;
  background:linear-gradient(135deg,#c9616b,#e9c8c2 55%,#b9848a);
  box-shadow:0 2px 6px rgba(0,0,0,.25)}
.body-text{font-size:12px;line-height:22px;color:var(--grey-text)}
.intro-text{left:229px;top:384px;width:514px}
.intro-text a{color:var(--blue-text);border-bottom:1px solid var(--blue-text)}
.section-title{left:79px;top:519px;font-size:18px;font-weight:400;color:#333}
.section-text{left:79px;top:542px;width:670px}

.sidebar{left:779px;top:146px;width:210px;height:549px;background:#fff;
  box-shadow:0 0 6px rgba(0,0,0,.22)}
.page-tools{left:21px;top:115px;font-size:12px;color:#444;line-height:22px}
.page-tools div{display:flex;align-items:center;gap:10px}
.side-heading{font-size:14px;font-weight:700;color:#555}
.side-list{list-style:none;font-size:12px;color:#555}
.side-list li{display:flex;align-items:center;gap:9px}
.side-list li::before{content:"";width:10px;height:10px;border-radius:50%;
  background:radial-gradient(circle,#fff 0 1.5px,transparent 2px),var(--blue)}

.footer-bar{left:0;top:695px;width:1024px;height:19px;
  background:linear-gradient(var(--blue-dark),var(--blue));
  box-shadow:0 -2px 4px rgba(0,0,0,.15);font-size:11px;color:#fff;padding:4px 0 0 85px}
.footer-bar a{margin:0 9px}
.footer{left:0;top:714px;width:1024px;height:144px;background:linear-gradient(#f3fbfe,var(--footer-bg))}
.footer-col{position:absolute;top:38px;font-size:12px;color:#555}
.footer-col h3{font-size:14px;margin-bottom:9px;color:#555}
.footer-col ul{list-style:none;line-height:18px}
.footer-col li{display:flex;align-items:center;gap:10px}
.footer-col li::before{content:"";width:9px;height:9px;border-radius:50%;background:#555}
.contact-lines{line-height:18px}
.contact-lines b{color:var(--blue)}
</style>
</head>
<body>
<div class="page">
  <header>
    <div class="abs brand"><span class="brand-mark"></span><span class="brand-name">Dentist's Office</span></div>
    <nav class="abs utility-links"><a href="#">home</a><a href="#">sitemap</a><a href="#">contact</a></nav>
    <div class="abs search">search...
      <svg width="12" height="12" viewBox="0 0 12 12"><circle cx="5" cy="5" r="3.8" fill="none" stroke="#999" stroke-width="1.5"/><line x1="8" y1="8" x2="11.5" y2="11.5" stroke="#999" stroke-width="1.8"/></svg>
    </div>
  </header>

  <nav class="abs main-nav">
    <a href="#" style="left:81px">home</a>
    <a href="#" style="left:155px">about us</a>
    <a href="#" style="left:248px">services</a>
    <a href="#" style="left:338px">menu item</a>
    <a href="#" style="left:430px"><span class="caret">&#9660;</span>menu item</a>
    <a href="#" class="active"><span class="caret">&#9660;</span>menu item</a>
    <a href="#" style="left:651px">contact</a>
  </nav>

  <div class="abs breadcrumb"><span>home</span><span>parent page</span><span class="current">current page</span></div>

  <main>
    <h1 class="abs page-title">Lorem ipsum dolar sit amet elit nam in</h1>
    <p class="abs lead"><span>Lorem ipsum dolor sit amet, consectetur adipiscing elit. Etiam hendrerit fringilla sodales.</span><br><span>Nulla pretium mattis mollis. Pellentesque eu tortor massa, vel lacinia libero. Nam in justo</span><br><span>non odio luctus iaculis sit amet vitae dolor. Morbi varius.</span></p>

    <div class="abs photo" role="img" aria-label="Close-up photo of a smile with a clear dental aligner being fitted"></div>
    <p class="abs body-text intro-text">In scelerisque magna nulla ut nunc. Aliquam erat volutpat. Donec at libero eros, vitae accumsan velit. Nam eu neque dolor. Nullam <a href="#">imperdiet quam sit amet</a> eros luctus id dignissim nulla tempus. Lorem vestibulum in massa ac ipsum pharetra faucibus. Duis ut leo felis. Cras ut laoreet urna. Fusce dignissim tempor tempor. Nunc ac sapien ligula, sed euismod nisi. Ut in lobortis urna. Ut rutrum elementum libero, quis eleifend dolor posuere blandit. Maecenas at tellus leo, id molestie</p>

    <h2 class="abs section-title">Lorem ipsum dolar sit amet</h2>
    <p class="abs body-text section-text">Quisque convallis erat urna, sit amet feugiat massa. Aenean auctor mauris id arcu venenatis tincidunt. Vivamus sollicitudin tincidunt suscipit. Phasellus lobortis magna eu mi lacinia ac dapibus ligula mattis. Phasellus malesuada nisi non nunc rutrum pellentesque. In porta hendrerit odio, ut vulputate urna tincidunt quis. Nulla malesuada tellus non lacus blandit gravida nec ut</p>
  </main>

  <aside class="abs sidebar">
    <div class="abs page-tools">
      <div><svg width="14" height="12" viewBox="0 0 14 12"><rect x="3" y="0" width="8" height="4" fill="#444"/><rect x="0" y="4" width="14" height="5" rx="1" fill="#444"/><rect x="3" y="7" width="8" height="5" fill="#fff" stroke="#444"/></svg>print this page</div>
      <div><svg width="14" height="10" viewBox="0 0 14 10"><rect x=".5" y=".5" width="13" height="9" fill="#444"/><polyline points="1,1 7,6 13,1" fill="none" stroke="#fff"/></svg>e-mail this page</div>
    </div>
    <h3 class="abs side-heading" style="left:21px;top:209px">Recent news</h3>
    <ul class="abs side-list" style="left:21px;top:239px;line-height:25.5px">
      <li>lorem ipsum</li><li>lorem ipsum dolar</li><li>lorem ipsum</li>
    </ul>
    <h3 class="abs side-heading" style="left:21px;top:345px">Archive</h3>
    <ul class="abs side-list" style="left:21px;top:372px;line-height:23px">
      <li>june</li><li>april</li><li>2009</li>
    </ul>
  </aside>

  <footer>
    <div class="abs footer-bar">(c) 2010 Dentist's Office All rights reserved <a href="#" style="margin-left:16px">Privacy Policy</a>|<a href="#">Security Statement</a>|<a href="#">Contact</a></div>
    <div class="abs footer">
      <div class="footer-col" style="left:81px"><h3>About Dentist's Office</h3><ul><li>lorem ipsum dolar sit</li><li>lorem ipsum dolar sit</li><li>lorem ipsum dolar sit</li></ul></div>
      <div class="footer-col" style="left:323px"><h3>Services</h3><ul><li>lorem ipsum dolar sit</li><li>lorem ipsum dolar sit</li><li>lorem ipsum dolar sit</li></ul></div>
      <div class="footer-col" style="left:561px"><h3>Address</h3><div class="contact-lines">5300 Alder Hollow Rd.<br>Fenwick, VA 23599-2430</div></div>
      <div class="footer-col contact-lines" style="left:798px;top:56px"><b>T</b> 0123 555 814<br><b>F</b> 0123 555 814<br>info@dentistoffice.example</div>
    </div>
  </footer>
</div>
</body>
</html>
```